Landing Page and Logo for Auto-Blogging Platform

I created a platform that allows users to start a blog for their business, hobby, charity, etc. I need a landing page where users can learn about the platform, benefits of consistent blogging, SEO value, plans/pricing, etc. The landing page needs to have multiple call to action buttons encouraging the visitor to register/sign up for a free trial.

In addition to the landing page, I need a page for users to establish the settings for their blog. This page should be a fairly simple form, intended for the user to enter a few details to set up their blog:
1. Name of Blog
2. Up to 10 topics and/or keywords the blog should focus on
3. Theme: Color-scheme and logo upload for blog.

I have attached the specifications of the platform's functionality so you can better understand how it works, plans/pricing, etc.

I also need a logo for the business. The name of the platform is PostNook.

Target Market(s)

Website owners, bloggers, business owners

Industry/Entity Type

Technology, Internet, web design

Coding

Coded - Design and coding required

Number of Pages Required

2 page

Colors
0054AA
0677BA
7BADD7
CADEEF
E8F1F8
0094D4
00A9DD
6FCCEA
C7EBF8
E9F6FB

Requirements
Must have
• Eye-catching design but fairly light on content (keep it simple and brief.)
Nice to have
• Eye-catching yet simple design, clean and easy to understand what we are offering.
Should not have
• Too much “wordy” and confusing content.

```html
<!DOCTYPE html>
<html lang="en">
<head>
<meta charset="utf-8">
<title>PostNook – Automate Your Blog Posting with AI</title>
<link href="https://fonts.googleapis.com/css2?family=Plus+Jakarta+Sans:wght@500;600;700;800&family=Lato:wght@400;700&display=swap" rel="stylesheet">
<style>
:root{
  --blue:#0054AA;
  --blue-2:#0677BA;
  --blue-soft:#7BADD7;
  --blue-pale:#CADEEF;
  --blue-mist:#E8F1F8;
  --ink:#111418;
  --text:#2b2f36;
  --muted:#5b616b;
  --grey-bg:#f3f4f6;
  --white:#fff;
}
*{box-sizing:border-box;margin:0;padding:0}
html,body{width:1200px;height:3929px;overflow:hidden}
body{font-family:"Lato",sans-serif;color:var(--text);background:var(--white);position:relative}
.accent{color:var(--blue)}
section,footer{position:relative;width:1200px;display:block}
.abs{position:absolute}

/* hero */
.hero{height:1060px;background:linear-gradient(180deg,var(--blue-mist) 0%,#f4f8fc 45%,#fff 100%)}
.brand{font-family:"Plus Jakarta Sans",sans-serif;font-weight:800;font-size:38px;color:var(--ink);letter-spacing:-.5px}
.hero .brand{left:110px;top:22px}
.nav{left:446px;top:36px;display:flex;gap:44px;font-family:"Plus Jakarta Sans",sans-serif;font-size:16px;font-weight:500;color:var(--ink)}
.nav .active{color:var(--blue);font-weight:700;border-bottom:2px solid var(--blue);padding-bottom:2px}
.btn{display:inline-flex;align-items:center;justify-content:center;gap:10px;background:var(--blue);color:#fff;font-family:"Plus Jakarta Sans",sans-serif;font-weight:700;border-radius:6px}
.register{left:951px;top:26px;width:138px;height:46px;font-size:16px}
.eyebrow{top:153px;width:100%;text-align:center;font-family:"Plus Jakarta Sans",sans-serif;font-weight:600;font-size:19px;color:var(--ink)}
.hero-title{top:196px;width:100%;text-align:center;font-family:"Plus Jakarta Sans",sans-serif;font-weight:800;font-size:50px;color:var(--ink)}
.hero-copy{top:276px;left:205px;width:790px;text-align:center;font-size:16px;line-height:31px;color:var(--text)}
.trial{left:494px;top:389px;width:212px;height:49px;font-size:15.5px}
.tablet{left:262px;top:497px;width:677px;height:516px;border-radius:30px;background:#1d1f22;padding:18px}
.tablet-screen{width:100%;height:100%;border-radius:14px;background:linear-gradient(160deg,#fbfbfc 0%,#e9edf2 55%,#d7dee8 100%)}

/* steps */
.steps{height:387px}
.section-title{width:100%;text-align:center;font-family:"Plus Jakarta Sans",sans-serif;font-weight:700;font-size:38px;color:var(--ink)}
.steps .section-title{top:74px}
.step{top:163px;width:260px;text-align:center}
.step-ring{position:relative;width:130px;height:130px;margin:0 auto;border-radius:50%;border:2px dashed var(--blue);display:flex;align-items:center;justify-content:center}
.step-core{width:104px;height:104px;border-radius:50%;background:#fff;box-shadow:0 4px 16px rgba(0,84,170,.18);display:flex;align-items:center;justify-content:center}
.step-num{position:absolute;left:0;bottom:8px;width:36px;height:36px;border-radius:50%;background:var(--blue);color:#fff;font-family:"Plus Jakarta Sans",sans-serif;font-weight:700;font-size:16px;display:flex;align-items:center;justify-content:center;border:3px solid #fff}
.step p{margin-top:26px;font-size:15.5px;line-height:26px;color:var(--text)}
.step-arrow{top:212px}

/* about */
.about{height:502px;display:flex}
.about-photo{width:602px;height:502px;background:linear-gradient(120deg,#e9e4de 0%,#d9cfc4 45%,#b69e87 75%,#efece8 100%)}
.about-panel{width:598px;height:502px;background:var(--blue);color:#fff;padding:58px 110px 0 60px}
.about-panel h2{font-family:"Plus Jakarta Sans",sans-serif;font-weight:700;font-size:40px;margin-bottom:26px}
.about-panel p{font-size:15.5px;line-height:26px;margin-bottom:25px}
.btn-light{display:inline-flex;align-items:center;justify-content:center;width:144px;height:51px;background:#fff;color:var(--blue);font-family:"Plus Jakarta Sans",sans-serif;font-weight:700;font-size:16px;border-radius:5px;margin-top:12px}

/* methods */
.methods{height:419px;background:var(--grey-bg)}
.methods .section-title{top:58px}
.method{top:175px;width:301px;height:151px;background:#fff;box-shadow:0 6px 20px rgba(0,0,0,.07);text-align:center;padding:60px 24px 0;font-size:17px;line-height:31px;color:var(--text)}
.method-icon{position:absolute;left:50%;top:-36px;margin-left:-36px;width:72px;height:72px;border-radius:50%;background:var(--blue);border:5px solid #fff;box-shadow:0 4px 12px rgba(0,0,0,.12);display:flex;align-items:center;justify-content:center}

/* pricing */
.pricing{height:660px}
.pricing .section-title{top:52px}
.plan{background:#fff;box-shadow:0 6px 26px rgba(0,0,0,.08);text-align:center}
.plan h3{font-family:"Plus Jakarta Sans",sans-serif;font-weight:600;font-size:20px;color:var(--ink)}
.plan .meta{font-size:15.5px;line-height:29px;color:var(--ink)}
.price{font-family:"Plus Jakarta Sans",sans-serif;font-weight:700;font-size:44px;color:var(--ink);line-height:54px}
.price small{font-family:"Lato",sans-serif;font-size:12px;font-weight:400;color:var(--muted)}
.features{list-style:none;text-align:left;display:inline-block;font-size:14px;color:var(--text)}
.features li{display:flex;align-items:center;gap:10px;height:29px}
.plan .btn{width:133px;height:45px;font-size:14.5px}
.plan-premium{border-bottom:3px solid var(--blue);z-index:2}
.plan-premium h3{color:var(--blue);font-size:23px;font-weight:700}
.plan-premium .features li{height:32px}

/* benefits */
.benefits{height:548px}
.benefits .section-title{top:56px}
.benefit-list{left:111px;top:128px;list-style:none;font-size:16.5px;color:var(--text)}
.benefit-list li{display:flex;align-items:center;gap:12px;height:43px}
.view-more{left:111px;top:410px;width:143px;height:50px;font-size:16px}
.benefit-photo{left:656px;top:144px;width:431px;height:316px;border:2px solid var(--blue);border-radius:10px;background:linear-gradient(135deg,#cfd8e0 0%,#a9b4bf 40%,#6e6357 70%,#2a2a2c 100%)}

/* footer */
.footer{height:353px;background:var(--grey-bg)}
.footer .brand{top:49px;left:0;width:100%;text-align:center;font-size:48px}
.footer-nav{top:140px;left:0;width:100%;display:flex;justify-content:center;gap:48px;font-family:"Plus Jakarta Sans",sans-serif;font-weight:500;font-size:17px;color:var(--ink)}
.copyright{top:197px;left:0;width:100%;text-align:center;font-family:"Plus Jakarta Sans",sans-serif;font-weight:600;font-size:14px;color:var(--ink)}
.payments{top:258px;left:0;width:100%;display:flex;justify-content:center;gap:48px;font-family:"Plus Jakarta Sans",sans-serif;font-weight:700;font-size:21px;color:#3b4252}
</style>
</head>
<body>

<section class="hero">
  <div class="abs brand">PostNook</div>
  <nav class="abs nav">
    <span class="active">Home</span><span>About the platform</span><span>Benefits</span><span>Pricing</span>
  </nav>
  <a class="abs btn register">Register
    <svg width="20" height="20" viewBox="0 0 20 20" fill="none" stroke="#fff" stroke-width="1.8"><rect x="2" y="2" width="11" height="15" rx="1.5"/><path d="M5 6h5M5 9h5M5 12h3"/><path d="M11 15l6-6 2 2-6 6h-2z"/></svg>
  </a>
  <div class="abs eyebrow">WELCOME TO POSTNOOK</div>
  <h1 class="abs hero-title">Automate Your Blog <span class="accent">Posting with AI</span></h1>
  <p class="abs hero-copy">Transform your blogging experience with our AI-powered platform that not only generates and optimizes content tailored to your audience but also continuously learns and adapts to deliver smarter insights, ensuring your voice stands out in a crowded digital landscape.</p>
  <a class="abs btn trial">Sign up for a free trial</a>
  <div class="abs tablet">
    <div class="tablet-screen" role="img" aria-label="Screenshot of a generated news blog homepage shown on a tablet"></div>
  </div>
</section>

<section class="steps">
  <h2 class="abs section-title">How to Set Up <span class="accent">the Auto-Blog</span></h2>

  <div class="abs step" style="left:96px">
    <div class="step-ring"><div class="step-core">
      <svg width="52" height="44" viewBox="0 0 52 44" stroke="#0054AA" stroke-width="3" stroke-linecap="round"><path d="M4 18v8M11 13v18M18 6v32M26 2v40M34 8v28M41 14v16M48 19v6"/></svg>
    </div><span class="step-num">1</span></div>
    <p>Select frequency of Automated<br>Blog Posts (daily, weekly, or monthly)</p>
  </div>
  <svg class="abs step-arrow" style="left:322px" width="58" height="18" fill="none" stroke="#9aa3ad" stroke-width="2"><path d="M2 12q26-12 52 0M46 6l8 6-9 3"/></svg>

  <div class="abs step" style="left:352px">
    <div class="step-ring"><div class="step-core">
      <svg width="46" height="44" viewBox="0 0 46 44" fill="none" stroke="#0054AA" stroke-width="3" stroke-linejoin="round"><path d="M30 6H8a4 4 0 0 0-4 4v26a4 4 0 0 0 4 4h26a4 4 0 0 0 4-4V20"/><path d="M18 28l2-8 18-18 6 6-18 18z"/><path d="M10 34h12"/></svg>
    </div><span class="step-num">2</span></div>
    <p>Name your blog</p>
  </div>
  <svg class="abs step-arrow" style="left:578px" width="58" height="18" fill="none" stroke="#9aa3ad" stroke-width="2"><path d="M2 6q26 12 52 0M46 1l8 5-8 5"/></svg>

  <div class="abs step" style="left:605px">
    <div class="step-ring"><div class="step-core">
      <svg width="48" height="48" viewBox="0 0 48 48" fill="none" stroke="#0054AA" stroke-width="2.5" stroke-linejoin="round"><rect x="4" y="6" width="40" height="28" rx="2"/><path d="M18 34l-2 8h16l-2-8M12 42h24M10 14h12M10 20h10M10 26h14"/><path d="M26 26l2-6 10-10 4 4-10 10z"/></svg>
    </div><span class="step-num">3</span></div>
    <p>Select your blog topics (or let AI<br>choose them for you)</p>
  </div>
  <svg class="abs step-arrow" style="left:832px" width="58" height="18" fill="none" stroke="#9aa3ad" stroke-width="2"><path d="M2 12q26-12 52 0M46 6l8 6-9 3"/></svg>

  <div class="abs step" style="left:860px">
    <div class="step-ring"><div class="step-core">
      <svg width="50" height="50" viewBox="0 0 50 50" fill="none" stroke="#0054AA" stroke-width="2.5"><ellipse cx="25" cy="25" rx="22" ry="9"/><ellipse cx="25" cy="25" rx="22" ry="9" transform="rotate(60 25 25)"/><ellipse cx="25" cy="25" rx="22" ry="9" transform="rotate(120 25 25)"/><text x="25" y="30" text-anchor="middle" font-family="Plus Jakarta Sans,sans-serif" font-size="13" font-weight="800" fill="#0054AA" stroke="none">AI</text></svg>
    </div><span class="step-num">4</span></div>
    <p>Go do something else &amp; let AI<br>do all your blogging for you!</p>
  </div>
</section>

<section class="about">
  <div class="about-photo" role="img" aria-label="Photo of a smiling woman reading on a tablet in a bright office"></div>
  <div class="about-panel">
    <h2>About PostNook</h2>
    <p>The platform will require a list of blog topics. Based on the topics list, the software will need to automatically send prompts to WriteEngine in the specified intervals (monthly, weekly, or daily), receive the blog content, and post it to the blog.</p>
    <p>Furthermore, the software will need some method of adding at least one image to each blog post. Ideally, this would be achieved by using the PixLoom API to retrieve image(s) based on keywords in the blog topic.</p>
    <a class="btn-light">Read More</a>
  </div>
</section>

<section class="methods">
  <h2 class="abs section-title">The blog <span class="accent">Using These Methods</span></h2>
  <div class="abs method" style="left:111px">
    <span class="method-icon"><svg width="34" height="34" viewBox="0 0 34 34" fill="none" stroke="#fff" stroke-width="2.2"><circle cx="17" cy="17" r="5"/><path d="M17 3v5M17 26v5M3 17h5M26 17h5M7 7l3.5 3.5M23.5 23.5L27 27M27 7l-3.5 3.5M10.5 23.5L7 27"/></svg></span>
    The user enters them into<br>a table manually.
  </div>
  <div class="abs method" style="left:450px">
    <span class="method-icon"><svg width="30" height="34" viewBox="0 0 30 34" fill="none" stroke="#fff" stroke-width="2.2" stroke-linejoin="round"><path d="M4 2h14l8 8v22H4z"/><path d="M18 2v8h8"/><circle cx="17" cy="23" r="6"/><path d="M17 26v-6M14 22l3-3 3 3"/></svg></span>
    The user uploads a list of blog<br>topics in CSV format.
  </div>
  <div class="abs method" style="left:788px">
    <span class="method-icon"><svg width="36" height="34" viewBox="0 0 36 34" fill="none" stroke="#fff" stroke-width="2.2" stroke-linejoin="round"><rect x="2" y="4" width="30" height="22" rx="2"/><path d="M12 26l-1 5h12l-1-5M8 31h18M7 11h10M7 16h8"/><path d="M18 20l2-5 9-9 3 3-9 9z"/></svg></span>
    Provide a list of 52 blog topics<br>for a handyman business's blog.
  </div>
</section>

<section class="pricing">
  <h2 class="abs section-title">Our Pricing <span class="accent">Plans</span></h2>

  <div class="abs plan" style="left:165px;top:160px;width:285px;height:453px;padding-top:44px">
    <h3>Base Plan</h3>
    <p class="meta" style="margin-top:18px">1 blog post<br>(up to 2,000 words)</p>
    <p class="price" style="margin-top:12px">$9.99<small>/month</small></p>
    <ul class="features" style="margin-top:14px">
      <li><svg width="13" height="11"><path d="M1 6l4 4 7-9" fill="none" stroke="#1d2a3a" stroke-width="2.2"/></svg>Reprehenderit in voluptate</li>
      <li><svg width="13" height="11"><path d="M1 6l4 4 7-9" fill="none" stroke="#1d2a3a" stroke-width="2.2"/></svg>Velit esse cillum dolore eu</li>
      <li><svg width="13" height="11"><path d="M1 6l4 4 7-9" fill="none" stroke="#1d2a3a" stroke-width="2.2"/></svg>Fugiat nulla pariatur</li>
      <li><svg width="13" height="11"><path d="M1 6l4 4 7-9" fill="none" stroke="#1d2a3a" stroke-width="2.2"/></svg>Mollit anim id est laborum</li>
    </ul>
    <div style="margin-top:20px"><a class="btn">Buy Now</a></div>
  </div>

  <div class="abs plan plan-premium" style="left:450px;top:137px;width:300px;height:498px;padding-top:34px">
    <h3>Premium Plan</h3>
    <p class="meta" style="margin-top:14px">1 blog post<br>(up to 2,000 words) every week</p>
    <p class="price" style="margin-top:12px">$14.99<small>/month</small></p>
    <ul class="features" style="margin-top:16px">
      <li><svg width="13" height="11"><path d="M1 6l4 4 7-9" fill="none" stroke="#0054AA" stroke-width="2.2"/></svg>Duis aute irure dolor in</li>
      <li><svg width="13" height="11"><path d="M1 6l4 4 7-9" fill="none" stroke="#0054AA" stroke-width="2.2"/></svg>Reprehenderit in voluptate</li>
      <li><svg width="13" height="11"><path d="M1 6l4 4 7-9" fill="none" stroke="#0054AA" stroke-width="2.2"/></svg>Velit esse cillum dolore eu</li>
      <li><svg width="13" height="11"><path d="M1 6l4 4 7-9" fill="none" stroke="#0054AA" stroke-width="2.2"/></svg>Fugiat nulla pariatur</li>
      <li><svg width="13" height="11"><path d="M1 6l4 4 7-9" fill="none" stroke="#0054AA" stroke-width="2.2"/></svg>Mollit anim id est laborum</li>
    </ul>
    <div style="margin-top:20px"><a class="btn" style="width:152px;height:46px">Buy Now</a></div>
  </div>

  <div class="abs plan" style="left:750px;top:160px;width:287px;height:453px;padding-top:44px">
    <h3>Ultimate Plan</h3>
    <p class="meta" style="margin-top:10px">1 blog post<br>(up to 3,000 words)<br>per day plus unlimited manual</p>
    <p class="price" style="margin-top:8px">$24.99<small>/month</small></p>
    <ul class="features" style="margin-top:12px">
      <li><svg width="13" height="11"><path d="M1 6l4 4 7-9" fill="none" stroke="#1d2a3a" stroke-width="2.2"/></svg>Reprehenderit in voluptate</li>
      <li><svg width="13" height="11"><path d="M1 6l4 4 7-9" fill="none" stroke="#1d2a3a" stroke-width="2.2"/></svg>Velit esse cillum dolore eu</li>
      <li><svg width="13" height="11"><path d="M1 6l4 4 7-9" fill="none" stroke="#1d2a3a" stroke-width="2.2"/></svg>Fugiat nulla pariatur</li>
      <li><svg width="13" height="11"><path d="M1 6l4 4 7-9" fill="none" stroke="#1d2a3a" stroke-width="2.2"/></svg>Mollit anim id est laborum</li>
    </ul>
    <div style="margin-top:16px"><a class="btn">Buy Now</a></div>
  </div>
</section>

<section class="benefits">
  <h2 class="abs section-title">Our <span class="accent">Benefits</span></h2>
  <ul class="abs benefit-list">
    <li><svg width="14" height="12"><path d="M1 6l4 4 8-9" fill="none" stroke="#0054AA" stroke-width="2.4"/></svg>Ut enim ad minim veniam, quis nostrud exercitation ullamco</li>
    <li><svg width="14" height="12"><path d="M1 6l4 4 8-9" fill="none" stroke="#0054AA" stroke-width="2.4"/></svg>Laboris nisi ut aliquip ex ea commodo consequat</li>
    <li><svg width="14" height="12"><path d="M1 6l4 4 8-9" fill="none" stroke="#0054AA" stroke-width="2.4"/></svg>Duis aute irure dolor in reprehenderit in voluptate velit esse</li>
    <li><svg width="14" height="12"><path d="M1 6l4 4 8-9" fill="none" stroke="#0054AA" stroke-width="2.4"/></svg>Cillum dolore eu fugiat nulla pariatur ad minim veniam</li>
    <li><svg width="14" height="12"><path d="M1 6l4 4 8-9" fill="none" stroke="#0054AA" stroke-width="2.4"/></svg>Lorem ipsum dolor sit amet, consectetur adipiscing elit, sed</li>
    <li><svg width="14" height="12"><path d="M1 6l4 4 8-9" fill="none" stroke="#0054AA" stroke-width="2.4"/></svg>Tempor incididunt ut labore et dolore magna aliqua.</li>
  </ul>
  <a class="abs btn view-more">View More</a>
  <div class="abs benefit-photo" role="img" aria-label="Photo of a woman typing a blog post on a laptop at a desk"></div>
</section>

<footer class="footer">
  <div class="abs brand">PostNook</div>
  <nav class="abs footer-nav"><span>Home</span><span>About the platform</span><span>Benefits</span><span>Pricing</span><span>Contact Us</span></nav>
  <p class="abs copyright">Copyrights@2024.PostNook.All Rights Reserved</p>
  <div class="abs payments"><span>Payvio</span><span>Coinly</span><span>TapWallet</span><span>QuickPay</span><span>CartPay</span></div>
</footer>

</body>
</html>
```